TALMORK

The business want a professional looking business card. We have a scetch we will add but want the extra upgrade, and would like more suggestions for variations of our business cards.

```html
<!DOCTYPE html>
<html lang="en">
<head>
<meta charset="UTF-8">
<title>TALMORK Business Card</title>
<link href="https://fonts.googleapis.com/css2?family=Montserrat:wght@400;500&display=swap" rel="stylesheet">
<style>
  :root {
    --backdrop: #43321f;
    --card: #f4f0e4;
    --card-glow: #faf8f1;
    --ink: #3b2a17;
    --gold: #b38d45;
    --gold-soft: #c7a565;
  }
  * { margin: 0; padding: 0; box-sizing: border-box; }
  html, body {
    width: 1200px; height: 805px; overflow: hidden;
    background: var(--backdrop);
    font-family: "Montserrat", Arial, sans-serif;
  }
  .canvas { position: relative; width: 1200px; height: 805px; }
  .card {
    position: absolute; top: 216px; width: 505px; height: 314px;
    background: var(--card);
  }
  .card-front { left: 68px; }
  .card-back {
    left: 626px;
    background: radial-gradient(ellipse at 50% 48%, var(--card-glow) 0%, var(--card) 70%);
  }
  .holder-name {
    position: absolute; left: 42px; top: 41px;
    font-size: 23px; font-weight: 500; color: var(--ink); letter-spacing: 0.2px;
  }
  .holder-role {
    position: absolute; left: 42px; top: 74px;
    font-size: 16px; font-weight: 400; color: var(--ink);
  }
  .contact-divider {
    position: absolute; left: 72px; top: 120px; width: 1px; height: 122px;
    background: var(--gold);
  }
  .contact-list { position: absolute; left: 32px; top: 121px; list-style: none; }
  .contact-item {
    display: flex; align-items: center; height: 31px;
    font-size: 15px; color: var(--ink);
  }
  .contact-icon { width: 22px; height: 22px; margin-right: 30px; flex: none; }
  .contact-icon svg { width: 22px; height: 22px; display: block; }
  .at-sign { font-size: 20px; line-height: 22px; text-align: center; color: var(--ink); }
  .brand-mark {
    position: absolute; left: 330px; top: 48px; width: 140px;
    display: flex; flex-direction: column; align-items: center;
  }
  .brand-dot {
    width: 88px; height: 88px; border-radius: 50%; background: var(--gold-soft);
  }
  .brand-name {
    margin-top: 16px; font-size: 20px; font-weight: 500;
    letter-spacing: 3px; color: var(--gold);
  }
  .back-lockup {
    position: absolute; left: 0; right: 0; top: 128px; text-align: center;
  }
  .back-name {
    font-size: 44px; font-weight: 500; letter-spacing: 7px; color: var(--gold);
    line-height: 1;
  }
  .back-tagline {
    margin-top: 12px; font-size: 13px; font-weight: 500;
    letter-spacing: 5px; color: var(--gold);
  }
</style>
</head>
<body>
<main class="canvas">
  <section class="card card-front">
    <h1 class="holder-name">Henrik Aas Lunde</h1>
    <p class="holder-role">CEO &amp; Founder</p>
    <div class="contact-divider"></div>
    <ul class="contact-list">
      <li class="contact-item">
        <span class="contact-icon">
          <svg viewBox="0 0 24 24" fill="none" stroke="#3b2a17" stroke-width="1.3" stroke-linejoin="round">
            <path d="M5 3h4l1.5 4.5-2.3 1.5a12 12 0 0 0 6.8 6.8l1.5-2.3L21 15v4a2 2 0 0 1-2 2A16 16 0 0 1 3 5a2 2 0 0 1 2-2z"/>
          </svg>
        </span>004791234567
      </li>
      <li class="contact-item">
        <span class="contact-icon">
          <svg viewBox="0 0 24 24" fill="none" stroke="#3b2a17" stroke-width="1.3">
            <rect x="3" y="6" width="18" height="12"/><path d="M3 6l9 7 9-7"/>
          </svg>
        </span>talmork.llc@mailbox.com
      </li>
      <li class="contact-item">
        <span class="contact-icon at-sign">@</span>talmork.llc@mailbox.com
      </li>
      <li class="contact-item">
        <span class="contact-icon">
          <svg viewBox="0 0 24 24" fill="none" stroke="#3b2a17" stroke-width="1.3">
            <circle cx="12" cy="12" r="9"/><ellipse cx="12" cy="12" rx="4" ry="9"/><path d="M3 12h18M5 7h14M5 17h14"/>
          </svg>
        </span>www.talmork.llc
      </li>
    </ul>
    <div class="brand-mark">
      <div class="brand-dot"></div>
      <span class="brand-name">TALMORK</span>
    </div>
  </section>
  <section class="card card-back">
    <div class="back-lockup">
      <p class="back-name">TALMORK</p>
      <p class="back-tagline">SINCE 2026</p>
    </div>
  </section>
</main>
</body>
</html>
```